Belvascotravel.com web design project + logo design

Hi,

We are a Russian online tour operator - sunkettle.com

We are looking to tranmsfer our domain to belvascotravel.com. The website and logo need to be belvascoesque - we are not looking to change our functionality, but we need to make the website much more attracitve to clients, much more wild looking but at the same time remaining a professional travel company.

The main concept of the website should be innovative travel (as belvasco was an innovator). Alternatively, you could go down the artist route and go down the draw / design your own tour road.

On our website the customer is able to combine travel services (hotels, flights, Visa services, and soon chauffeur, car rental etc...) put it into their basket (the basket definitely has to look better than it is at the moment) and pay for it in one go by card.

We are also stressin our customer support with web chat, call centre etc... (call centre number at the top of the page)

We aim to provide an easy user experience, but we need to make it have some more style, so I will be waiting for what you guys can come up with.
Let me know if you have any questions - skype is: mrdolbarin

Industry/Entity Type

It Company

Requirements
Must have
• It is quite a simple task - to take the existing website sunkettle.com and belvascosize it to create belvascotravel.com, the functionality of the website will remain the same and there are not many pages in the website. Homepage, Checkout step1, Checkout step 2 (you can view both of these if you select a service) and the generic pages for T&C''s, Privacy policy etc...

IMPORTANT UPDATE

We are also looking at how the search results will look in the designs, (please do a search on our website for hotel / flight)

```html
<!DOCTYPE html>
<html lang="en">
<head>
<meta charset="utf-8">
<title>Belvasco Travel</title>
<link href="https://fonts.googleapis.com/css2?family=Fira+Sans:wght@400;500&family=Source+Sans+3:wght@400;600&display=swap" rel="stylesheet">
<style>
:root{
  --nav:#4a74c4;
  --nav-line:#6a8fd6;
  --teal:#0f7f96;
  --green:#2a9a3a;
  --green-dark:#1f7d2c;
  --text:#8a8a8a;
  --dark:#2a2f38;
  --footer:#2c313a;
  --footer-line:#3c424c;
  --panel:rgba(30,32,36,.88);
}
*{box-sizing:border-box;margin:0;padding:0}
html,body{width:935px;height:1200px;overflow:hidden;background:#fff}
body{position:relative;font-family:"Source Sans 3",Arial,sans-serif;color:var(--text)}
.hero{position:absolute;left:0;top:0;width:935px;height:528px;background:linear-gradient(180deg,#7c96b4 0%,#9aa6b0 30%,#6d6f68 55%,#6f8a3c 80%,#5d7a2e 100%)}
.logo{position:absolute;left:94px;top:0;width:142px;height:80px;background:#fff;display:flex;align-items:center;justify-content:center;gap:5px}
.logo span{font:500 13px "Fira Sans",sans-serif;color:#1e4f9a}
.logo i{width:12px;height:12px;border-radius:50%;background:#1e4f9a;display:block}
.nav{position:absolute;left:236px;top:0;width:606px;height:80px;display:flex;background:var(--nav);border-top:2px solid var(--nav-line)}
.nav a{flex:auto;display:flex;flex-direction:column;align-items:center;justify-content:center;gap:8px;color:#fff;text-decoration:none;font-size:12.5px;font-weight:600;border-left:1px solid var(--nav-line)}
.nav svg{width:20px;height:20px;fill:#fff}
.search{position:absolute;left:94px;top:91px;width:249px;height:286px;background:var(--panel);padding:10px 8px;color:#fff}
.search h1{font:400 21px "Fira Sans",sans-serif;letter-spacing:.3px}
.search p{font:400 13.5px/19px "Fira Sans",sans-serif;margin-bottom:10px}
.field{height:23px;background:#fff;color:#555;font-size:10.5px;padding:4px 11px;margin-bottom:10px;position:relative}
.field:after{content:"";position:absolute;right:0;top:0;border-top:8px solid #2a9fd8;border-left:8px solid transparent}
.pair{display:flex;gap:9px}.pair .field{flex:1;margin-top:2px}
.check{font-size:9.5px;display:flex;align-items:center;gap:8px;margin-top:-1px;height:14px}
.check b{width:9px;height:9px;background:#ddd;display:block;font-size:8px;line-height:9px;color:#333;text-align:center}
.cta{display:block;margin:8px auto 0;width:128px;height:29px;background:var(--green);color:#fff;font:500 12px/29px "Fira Sans",sans-serif;text-align:center}
.gallery{position:absolute;left:62px;top:377px;width:812px;height:139px;background:rgba(30,30,30,.75)}
.thumb{position:absolute;top:0;width:249px;height:139px}
.arrow{position:absolute;top:54px;width:14px;height:32px;fill:#ccc}
.section-title{border-left:3px solid var(--teal);padding-left:11px;color:var(--teal);font:500 19px "Fira Sans",sans-serif}
.services{position:absolute;left:94px;top:538px;width:748px}
.services .lede{font-size:10.5px;color:#555;margin-top:3px}
.tabs{position:absolute;top:47px;left:0;width:748px;height:39px;display:flex;background:linear-gradient(#f3f3f3,#ddd)}
.tab{flex:1;display:flex;align-items:center;gap:14px;padding-left:14px;font:500 13px "Fira Sans",sans-serif;color:#444;border-right:1px solid #ccc}
.tab svg{width:22px;height:18px;fill:#555}
.tab.on{background:var(--green);color:#fff;flex:0 0 189px}.tab.on svg{fill:#fff}
.panel{position:absolute;top:86px;left:0;width:748px;height:150px;border:1px solid #e6e6e6;border-top:0}
.panel:before{content:"";position:absolute;left:0;top:0;border-top:10px solid var(--green-dark);border-right:10px solid transparent}
.panel p{position:absolute;left:17px;top:10px;width:480px;font-size:10.5px;line-height:17px}
.panel a{position:absolute;left:18px;top:126px;font-size:11px;font-weight:600;color:#1f6fb0}
.panel .pic{position:absolute;left:520px;top:10px;width:215px;height:128px;background:linear-gradient(120deg,#2b3a55,#7a9bbd 55,#e6e2d6)}
.welcome{position:absolute;left:94px;top:793px;width:500px}
.welcome p{padding-left:12px;font-size:10.5px;line-height:18px;margin-top:8px}
.testi{position:absolute;left:614px;top:793px;width:228px}
.person{display:flex;gap:8px;margin:10px 0 0 13px}
.avatar{width:36px;height:36px;flex:none;background:linear-gradient(#ddd,#999)}
.person h3{font-size:10px;font-weight:400;color:var(--green)}
.person p{font-size:10px;line-height:15.5px;color:#aaa;margin-top:2px}
footer{position:absolute;left:0;top:999px;width:935px;height:201px;background:var(--footer);color:#d6d8dc}
.col{position:absolute;top:17px;font-size:10.5px;line-height:18px}
.col h4{font:400 12.5px "Source Sans 3",sans-serif;color:#fff;margin-bottom:8px}
.sep{position:absolute;top:47px;width:1px;height:103px;background:var(--footer-line)}
.bottom{position:absolute;left:0;top:161px;width:935px;border-top:1px solid var(--footer-line);padding:12px 94px;display:flex;justify-content:space-between;font-size:10.5px}
</style>
</head>
<body>
<header class="hero" role="img" aria-label="Mountain landscape with snowy peaks and a red train on green slopes">
  <div class="logo"><i></i><span>belvascotravel.com</span></div>
  <nav class="nav">
    <a href="#"><svg viewBox="0 0 20 20"><path d="M10 2 1 10h3v8h5v-5h2v5h5v-8h3z"/></svg>Home</a>
    <a href="#"><svg viewBox="0 0 20 20"><path d="M10 1a6 6 0 0 0-6 6c0 5 6 12 6 12s6-7 6-12a6 6 0 0 0-6-6zm0 8.5A2.5 2.5 0 1 1 10 4.5a2.5 2.5 0 0 1 0 5z"/></svg>Destinations</a>
    <a href="#"><svg viewBox="0 0 20 20"><circle cx="13" cy="3" r="2"/><path d="M9 6h4l2 4 3 1-1 2-4-1-1-2-1 3 3 3-1 3-4-4-2 4H4l3-6 1-4-2 1-1 3-2-1 2-4z"/></svg>Activities</a>
    <a href="#"><svg viewBox="0 0 20 20"><path d="M10 6C7 2 2 3 1 6c3-1 6 0 8 1-3 0-6 3-5 6 2-3 4-4 5-5l-1 11h3l-1-11c1 1 3 2 5 5 1-3-2-6-5-6 2-1 5-2 8-1-1-3-6-4-9 0z"/></svg>Trip Style</a>
    <a href="#"><svg viewBox="0 0 20 20"><path d="M7 3h6v3h5v11H2V6h5zm2 1v2h2V4z"/></svg>Responsible Travel</a>
    <a href="#"><svg viewBox="0 0 20 20"><path d="M1 4h18v2l-9 6-9-6zm0 4 9 6 9-6v8H1z"/></svg>Contact Us</a>
  </nav>
  <form class="search">
    <h1>FIND A PLACE TO STAY</h1>
    <p>Lorem Ipsum est simplement du faux text Lorem Ipsum est</p>
    <div class="field">Where do you want to go?</div>
    <div class="field">Persons</div>
    <div class="field">Range</div>
    <div class="pair"><div class="field">Lorem Ipsum</div><div class="field">Lorem Ipsum</div></div>
    <div class="check"><b></b>Обратно</div>
    <div class="check"><b>✓</b>В одну сторону</div>
    <span class="cta">GET YOURS NOW</span>
  </form>
  <div class="gallery">
    <svg class="arrow" style="left:10px" viewBox="0 0 14 32"><path d="M12 0v32L0 16z"/></svg>
    <div class="thumb" style="left:32px;background:linear-gradient(120deg,#e8e4dc,#f4efe4 50%,#3e9ed8)" role="img" aria-label="Woman relaxing in a beach chair by the sea"></div>
    <div class="thumb" style="left:281px;background:linear-gradient(160deg,#5aa6d6,#2fc7cf 55%,#1a8fc0)" role="img" aria-label="Hammock under palm trees over turquoise water"></div>
    <div class="thumb" style="left:530px;width:250px;background:linear-gradient(160deg,#5a5e56,#c9cec8 60%,#eef0ee)" role="img" aria-label="Snowy tree-lined country road in winter"></div>
    <svg class="arrow" style="right:10px" viewBox="0 0 14 32"><path d="M2 0v32l12-16z"/></svg>
  </div>
</header>

<section class="services">
  <h2 class="section-title">Our Services</h2>
  <p class="lede" style="padding-left:14px">Lorem ipsum est simplement du faux texte employé dans la sition et la misen page avant impression employé sition et la misen page avant impression.</p>
  <div class="tabs">
    <div class="tab on"><svg viewBox="0 0 22 18"><circle cx="15" cy="2" r="2"/><path d="M10 5h5l2 4 4 1-1 2-5-1-1-2-1 3 3 3-1 3-4-4-2 4H5l3-6 1-4-2 1-1 3-2-1 2-4z"/></svg>Visa Service</div>
    <div class="tab"><svg viewBox="0 0 22 18"><path d="M1 10h8l5-7h2l-3 7h6l2-2h1l-1 3 1 3h-1l-2-2h-6l3 7h-2l-5-7H1z"/></svg>Flights Service</div>
    <div class="tab"><svg viewBox="0 0 22 18"><path d="M1 3h2v6h6V6h10a2 2 0 0 1 2 2v8h-2v-3H3v3H1z"/><circle cx="6" cy="6" r="2"/></svg>Hotel Service</div>
    <div class="tab"><svg viewBox="0 0 22 18"><path d="M3 1 1 3l7 7-5 5 2 2 5-5 5 5 2-2-5-5 2-2a4 4 0 0 0 5-5l-3 2-2-2 2-3a4 4 0 0 0-5 5l-2 2z"/></svg>Other Services</div>
  </div>
  <div class="panel">
    <p>Lorem Ipsum est simplement du faux texte employé dans la sition et la misen page avant impression. Le Lorem Ipsum est le faux texte standard de l'imprimerie depuis les années 1500, quand un peintre anonyme assembla ensemble des morceaux de texte pour réaliser un livre spécimen de polices de texte. Il n'a pas fait que survivre cinq siècles, mais s'est aussi adapté à la bureautique informatique, sans que son contenu n'en soit modifié.<br>Il n'a pas fait que survivre cinq siècles, mais s'est aussi adapté à la bureautique informatique.</p>
    <a href="#">View Detail</a>
    <div class="pic" role="img" aria-label="Passport, globe, city skyline and travel map collage"></div>
  </div>
</section>

<section class="welcome">
  <h2 class="section-title">Welcome to Belvasco Travel</h2>
  <p>Lorem Ipsum est simplement du faux texte employé dans la sition et la misen page avant impression. Le Lorem Ipsum est le faux texte standard de l'imprimerie depuis les années 1500, quand un peintre anonyme assembla ensemble des morceaux de texte pour réaliser un livre spécimen de polices de texte.</p>
  <p>Il n'a pas fait que survivre cinq siècles, mais s'est aussi adapté à la bureautique informatique, sans que son contenu n'en soit modifié. Il a été popularisé dans les années 1960.<br>grâce à la vente de feuilles Lettrafix contenant des passages du Lorem Ipsum, et, plus récemment, par son inclusion dans des applications de mise en page de texte, comme Orvel PageComposer.</p>
</section>

<aside class="testi">
  <h2 class="section-title">Testimonials</h2>
  <div class="person"><div class="avatar" role="img" aria-label="Customer portrait"></div><div><h3>Corwin Maddell</h3><p>"Lorem ipsum dolor sit nsectetuer adipiscing elit, sed diam nummy nibh euismod."</p></div></div>
  <div class="person"><div class="avatar" role="img" aria-label="Customer portrait"></div><div><h3>Tobias Renner</h3><p>"Lorem ipsum dolor sit nsectetuer adipiscing elit, sed diam nummy nibh specimen de polices euismod."</p></div></div>
</aside>

<footer>
  <div class="col" style="left:95px"><h4>DESTINATIONS:</h4>Europe<br>North America<br>South America<br>Africa<br>Asia<br>Australia</div>
  <div class="sep" style="left:228px"></div>
  <div class="col" style="left:278px"><h4>SITE MAP</h4>Home<br>Activites<br>Trip Styles<br>Responsible Travel</div>
  <div class="sep" style="left:424px"></div>
  <div class="col" style="left:455px"><h4>OUR SERVICES</h4>Lorem ipsum dolor<br>Sit amet consecteture<br>Adipisicing elit<br>Son inclusin dans des</div>
  <div class="sep" style="left:646px"></div>
  <div class="col" style="left:680px"><h4>CONTACT INFORMATIONS:</h4>E-mail: hello@belvascotravel.com<br>Phone: +47 51 20 44 83<br>Opening hours:<br>Mon - Fri: 09.00 - 21.00<br>Sat: 12.00 - 16.00<br>Sun: 12.00 - 14.00</div>
  <div class="bottom"><span>Copyright 2013 Website Name. All Rights Reserved.</span><span>Privacy Policy | Terms &amp; Condition</span></div>
</footer>
</body>
</html>
```